Brand New Product Needs Sales Focused Website Design

Looking for design of Homepage, Category Page & Product Page for single product sales focused website. TrundleCrate manufacture and distribute a brand new product to the market called PalTote-Case which is a super strong, re-useable, folding & stacking plastic box which can be seen on our current website www.paltote-case.example PalTote-Case was originally developed as an alternative to supermarket carrier bags and was pitched as a box for life against the other low end re-useable products. The original version was made from recycled plastic and pitched very much as environmental product. We are now taking a different direction and have re-designed the boxes in 5 bright and fashionable designs and although we still want the primary focus to be supermarket shopping we want to position the product as a design led, must have shopping and household accessory rather than a boring, cheap looking black plastic box. The new designs will still have the environmental benefits of being able to be re-used thousands of times and being 100% recyclable and save on the imminent 5p tax on carrier bags in the UK however the new designs will not be made from recycled material. Although the main use for PalTote-Case is supermarket shopping it has a multitude of other uses especially where you need temporary storage - laundry, back of the car, moving house/students, gardening, days out, home office filing (will take A4 file), recycling and much more - PalTote-Case is made out of super strong Polypropylene and can be easily washed and sanitised after use and can be folded and unfolded thousands of times and so will last for many years. PalTote-Case is a product that needs to be seen in action to be understood so the web design must quickly and easily communicate what PalTote-Case is and how it works - this can be done with video, images and copy. Our current website does not work for many reasons:- it is too busy, has too much information, tries too hard and ultimately isn't working. Any of the images off our current website can be supplied for use. Once the concept of the website is agreed I can get these photoshopped with the new designs. Pictures of new designs for reference will be attached to this brief. Ultimately we want the website to convert visitors to sales and therefore designers with a proven track record in this field are especially welcome to enter. We also have a Dropbox folder with over 100 product and situation images in - please send email address and we will send an invite to the folder. Due to Christmas period this competition will be run over 15 days however we may choose to extend the deadline to account for the non working days. Any questions feel free to ask - we will respond within 24 hours where possible.

```html
<!DOCTYPE html>
<html lang="en">
<head>
<meta charset="utf-8">
<title>PalTote-Case – Home</title>
<link rel="stylesheet" href="https://fonts.googleapis.com/css2?family=Raleway:wght@400;500;600;700&family=Open+Sans:wght@400;600&display=swap">
<style>
  :root {
    --teal: #0b98c0;
    --page: #eeeeee;
    --white: #ffffff;
    --ink: #222426;
    --muted: #6f6f6f;
    --footer: #3a3a3f;
    --footer-line: #4a4a50;
    --footer-text: #9a9aa0;
    --footer-head: #ffffff;
    --orange: #f58220;
    --card-line: #e3e3e3;
    --icon-bg: #26262a;
    --icon-line: #e8e8e8;
  }
  * { box-sizing: border-box; margin: 0; padding: 0; }
  html, body { width: 895px; height: 1200px; overflow: hidden; }
  body {
    position: relative;
    background: var(--page);
    font-family: "Raleway", sans-serif;
    color: var(--ink);
  }
  .abs { position: absolute; }

  /* Header */
  .topbar { left: 0; top: 0; width: 895px; height: 43px; background: var(--teal); }
  .nav { left: 291px; top: 15px; font-family: "Open Sans", sans-serif; font-size: 10.5px; color: var(--white); }
  .nav a { color: inherit; text-decoration: none; position: absolute; white-space: nowrap; }
  .brand {
    left: 82px; top: 0; width: 175px; height: 109px; background: var(--white);
    display: flex; flex-direction: column; align-items: center; justify-content: center; gap: 9px;
    z-index: 3;
  }
  .brand-dot { width: 32px; height: 32px; border-radius: 50%; background: var(--teal); }
  .brand-name { font-weight: 700; font-size: 20px; color: var(--teal); }

  .hero {
    left: 82px; top: 43px; width: 731px; height: 293px;
    background:
      radial-gradient(ellipse 150px 120px at 540px 170px, rgba(255,255,255,.95), rgba(255,255,255,0) 100%),
      radial-gradient(ellipse 90px 60px at 470px 30px, rgba(80,170,110,.75), rgba(80,170,110,0) 100%),
      radial-gradient(ellipse 80px 140px at 700px 120px, rgba(214,70,110,.75), rgba(214,70,110,0) 100%),
      radial-gradient(ellipse 60px 120px at 731px 60px, rgba(70,120,200,.7), rgba(70,120,200,0) 100%),
      radial-gradient(ellipse 180px 90px at 120px 260px, rgba(120,120,126,.6), rgba(120,120,126,0) 100%),
      linear-gradient(180deg, #d6d4d6 0%, #c4c1c3 60%, #9c999b 100%);
  }
  .search-panel { left: 584px; top: 44px; width: 210px; height: 38px; background: var(--teal); z-index: 2; }
  .search-input { left: 8px; top: 7px; width: 162px; height: 25px; background: var(--white); font-family: "Open Sans", sans-serif; font-size: 9.5px; color: #333; padding: 6px 9px; }
  .search-icon { left: 180px; top: 6px; }
  .welcome { left: 82px; top: 175px; width: 385px; height: 91px; background: var(--teal); color: var(--white); padding: 11px 0 0 40px; }
  .welcome h1 { font-weight: 400; font-size: 23.5px; line-height: 1.2; }
  .welcome h1 strong { font-weight: 700; }
  .welcome p { font-size: 9.6px; line-height: 18px; margin-top: 5px; width: 290px; }

  .tagline { left: 82px; top: 336px; width: 731px; height: 50px; background: var(--teal); }
  .tagline h2 { position: absolute; left: 20px; top: 6px; font-weight: 400; font-size: 29px; color: var(--white); white-space: nowrap; }
  .btn-shop { position: absolute; left: 537px; top: 10px; width: 123px; height: 29px; background: var(--white);
    color: var(--teal); font-weight: 600; font-size: 12.5px; display: flex; align-items: center; justify-content: center; }

  /* Content */
  .content { left: 82px; top: 394px; width: 731px; height: 608px; background: var(--white); }
  .card { top: 413px; width: 161px; height: 297px; border: 1px solid var(--card-line); background: var(--white); }
  .card-photo { width: 161px; height: 134px; margin: -1px 0 0 -1px; }
  .badge-new { position: absolute; left: 17px; top: 20px; background: var(--teal); color: var(--white); font-family: "Open Sans", sans-serif; font-size: 8.5px; font-weight: 600; padding: 2px 5px; }
  .card h3 { font-weight: 500; font-size: 13.5px; margin: 17px 0 0 17px; }
  .card p { font-size: 9.5px; line-height: 14px; color: var(--muted); margin: 9px 10px 0 17px; }
  .btn-cart { position: absolute; left: 17px; top: 250px; width: 124px; height: 30px; background: var(--teal); color: var(--white);
    font-weight: 500; font-size: 12.5px; display: flex; align-items: center; justify-content: center; }

  .video { left: 104px; top: 745px; width: 321px; height: 232px; overflow: hidden;
    background:
      radial-gradient(ellipse 60px 90px at 265px 110px, rgba(150,80,200,.55), rgba(150,80,200,0) 100%),
      radial-gradient(ellipse 110px 40px at 90px 175px, rgba(140,110,70,.6), rgba(140,110,70,0) 100%),
      linear-gradient(180deg, #f4f4f4 0%, #e2e2e2 55%, #9a9793 100%); }
  .video-frame { position: absolute; inset: 0; }
  .play { position: absolute; left: 134px; top: 86px; width: 55px; height: 35px; background: #3a3b3c; border-radius: 3px; }
  .controls { position: absolute; left: 0; bottom: 0; width: 321px; height: 33px; background: #121212; }
  .controls .track { position: absolute; left: 0; top: 0; width: 321px; height: 2px; background: #444; }
  .controls .track i { position: absolute; left: 0; top: 0; width: 210px; height: 2px; background: #e2231a; }
  .time { position: absolute; left: 46px; top: 13px; font-family: "Open Sans", sans-serif; font-size: 6.5px; color: #bbb; }

  .intro { left: 489px; top: 745px; width: 318px; }
  .intro h2 { font-weight: 400; font-size: 22.5px; line-height: 28px; }
  .intro p { font-size: 9.6px; line-height: 18px; color: var(--muted); margin-top: 21px; }

  /* Footer */
  .footer { left: 0; top: 1002px; width: 895px; height: 198px; background: var(--footer); font-family: "Open Sans", sans-serif; }
  .foot-col { top: 20px; }
  .foot-col h4 { font-size: 11.5px; font-weight: 600; color: var(--footer-head); margin-bottom: 4px; }
  .foot-col a { display: block; font-size: 9.5px; line-height: 16.5px; color: var(--footer-text); text-decoration: none; }
  .foot-col p { font-size: 9.5px; line-height: 16.5px; color: var(--footer-text); width: 185px; }
  .newsletter { left: 626px; top: 76px; width: 186px; height: 24px; display: flex; }
  .newsletter .email { width: 127px; background: #f2f2f2; font-size: 7.5px; font-style: italic; color: #888; padding: 8px 9px; }
  .newsletter .subscribe { width: 59px; background: var(--orange); color: var(--white); font-size: 9.5px; font-weight: 600; display: flex; align-items: center; justify-content: center; }
  .follow { left: 626px; top: 110px; font-size: 11.5px; font-weight: 600; color: var(--footer-head); }
  .socials { left: 625px; top: 132px; display: flex; gap: 5px; }
  .social-icon { width: 19px; height: 19px; border-radius: 50%; background: var(--icon-bg); display: flex; align-items: center; justify-content: center; }
  .foot-rule { left: 0; top: 164px; width: 895px; height: 1px; background: var(--footer-line); }
  .copyright { left: 0; top: 176px; width: 895px; text-align: center; font-size: 9px; color: var(--footer-text); }
</style>
</head>
<body>

<header>
  <div class="abs topbar"></div>
  <div class="abs brand">
    <span class="brand-dot"></span>
    <span class="brand-name">PalTote-Case</span>
  </div>
  <nav class="abs nav">
    <a style="left:0">HOME</a>
    <a style="left:59px">CATAGORY</a>
    <a style="left:141px">OUR RANGE</a>
    <a style="left:224px">GAURANTEE</a>
    <a style="left:313px">PRODUCTS</a>
    <a style="left:398px">CONTACT US</a>
  </nav>
</header>

<section>
  <div class="abs hero" role="img" aria-label="Shopper carrying a floral patterned folding box in a supermarket aisle"></div>
  <div class="abs search-panel">
    <div class="abs search-input">Search</div>
    <svg class="abs search-icon" width="24" height="26" viewBox="0 0 24 26">
      <circle cx="9" cy="9" r="7" fill="none" stroke="#fff" stroke-width="3"/>
      <line x1="14" y1="14.5" x2="21" y2="22" stroke="#fff" stroke-width="4" stroke-linecap="round"/>
    </svg>
  </div>
  <div class="abs welcome">
    <h1>Welcome to <strong>PalTote-Case</strong></h1>
    <p>Lorem ipsum dolor sit amet consectetur adipiscing elit sed do eiusmod tempor incididunt ut la magna aliqua.</p>
  </div>
  <div class="abs tagline">
    <h2>Ingenious And Practical Box For Life</h2>
    <div class="btn-shop">Shop Now</div>
  </div>
</section>

<main>
  <div class="abs content"></div>

  <article class="abs card" style="left:100px">
    <div class="card-photo" role="img" aria-label="Floral patterned folding box on a carpet" style="background:linear-gradient(180deg,#c9c9c9 0%,#ecebe6 14%,#e4d6c4 30%,#d9c0b0 58%,#c9b6a6 72%,#6e756b 82%,#5f665d 100%)"></div>
    <span class="badge-new">NEW</span>
    <h3>Lorem Ipsum</h3>
    <p>Lorem ipsum dolor sit amet, consectetutempor incididunt ut labore et dolore magna aliqua.</p>
    <div class="btn-cart">Add to Cart</div>
  </article>
  <article class="abs card" style="left:278px">
    <div class="card-photo" role="img" aria-label="Wood effect folding box on a carpet" style="background:linear-gradient(180deg,#bdbcba 0%,#efefed 12%,#a17a58 26%,#8a6344 55%,#7a573b 74%,#606759 84%,#545a4f 100%)"></div>
    <span class="badge-new">NEW</span>
    <h3>Lorem Ipsum</h3>
    <p>Lorem ipsum dolor sit amet, consectetutempor incididunt ut labore et dolore magna aliqua.</p>
    <div class="btn-cart">Add to Cart</div>
  </article>
  <article class="abs card" style="left:456px">
    <div class="card-photo" role="img" aria-label="Pale blue dotted folding box on a carpet" style="background:linear-gradient(180deg,#d6d7d9 0%,#f4f5f6 22%,#b9c8d6 40%,#a9bccd 66%,#8fa1b1 78%,#5f665d 86%,#545a4f 100%)"></div>
    <span class="badge-new">NEW</span>
    <h3>Lorem Ipsum</h3>
    <p>Lorem ipsum dolor sit amet, consectetutempor incididunt ut labore et dolore magna aliqua.</p>
    <div class="btn-cart">Add to Cart</div>
  </article>
  <article class="abs card" style="left:634px">
    <div class="card-photo" role="img" aria-label="Dark wood effect folding box" style="background:linear-gradient(180deg,#3a2a20 0%,#4a3324 12%,#7c5638 30%,#8a6242 55%,#6e4c33 80%,#5a3e2b 100%)"></div>
    <span class="badge-new">NEW</span>
    <h3>Lorem Ipsum</h3>
    <p>Lorem ipsum dolor sit amet, consectetutempor incididunt ut labore et dolore magna aliqua.</p>
    <div class="btn-cart">Add to Cart</div>
  </article>

  <div class="abs video">
    <div class="video-frame" role="img" aria-label="Product demo video still with a presenter holding a folded box beside a shopping trolley"></div>
    <div class="play">
      <svg width="55" height="35" viewBox="0 0 55 35"><polygon points="22,10 22,25 35,17.5" fill="#fff"/></svg>
    </div>
    <div class="controls">
      <div class="track"><i></i></div>
      <svg class="abs" style="left:14px;top:12px" width="10" height="10" viewBox="0 0 10 10">
        <rect x="2" y="1" width="2" height="8" fill="#ddd"/><rect x="6" y="1" width="2" height="8" fill="#ddd"/>
      </svg>
      <span class="time">00:54:21 / 01:42:30</span>
      <svg class="abs" style="left:213px;top:11px" width="70" height="12" viewBox="0 0 70 12">
        <path d="M4 2v6.5a2 2 0 1 1-1-1.7V2h4v1.5H4z" fill="#ddd"/>
        <rect x="14" y="5" width="36" height="2" fill="#e2231a"/>
        <rect x="50" y="5" width="10" height="2" fill="#555"/>
      </svg>
      <svg class="abs" style="left:297px;top:11px" width="11" height="11" viewBox="0 0 11 11">
        <path d="M1 1l3.5 3.5M10 1L6.5 4.5M1 10l3.5-3.5M10 10L6.5 6.5" stroke="#ddd" stroke-width="1.4"/>
      </svg>
    </div>
  </div>

  <div class="abs intro">
    <h2>Lorem ipsum dolor sit amet Consectutuer</h2>
    <p>Lorem ipsum dolor sit amet, consectetur adipiscing elit, sed do eiusmod tempor incididunt ut labore et dolore magna aliqua. Ut enim ad minim veniam, quis nostrud exercitation ullamco laboris nisi ut aliquip ex ea commodo consequat. Duis aute irure dolor in reprehenderit in voluptate velit esse cillum dolore eu fugiat nulla pariatur Excepteur sint occaecat cupidatat non proident, sunt in culpa qui officia deserunt mollit anim id est laborum aliquip ex ea voluptate velit esse cillum dolore e</p>
  </div>
</main>

<footer class="abs footer">
  <div class="abs foot-col" style="left:81px">
    <h4>Site Links</h4>
    <a>Home</a><a>About Us</a><a>Shop Our Products</a><a>Need Help</a>
  </div>
  <div class="abs foot-col" style="left:213px">
    <h4>About PalTote Case</h4>
    <a>Our Mission</a><a>Blog</a><a>Why Choose Us</a>
  </div>
  <div class="abs foot-col" style="left:352px">
    <h4>Our Boxes</h4>
    <a>Watch A Live Demo</a><a>View Our Products</a><a>Smartphone Apps</a>
  </div>
  <div class="abs foot-col" style="left:489px">
    <h4>Having Trouble?</h4>
    <a>Knowledge Base</a><a>Discussion Forum</a><a>Contact Us</a>
  </div>
  <div class="abs foot-col" style="left:626px">
    <h4>Our Newsletter</h4>
    <p>Subscribe To Our E-mail List for Sales &amp; Updates.</p>
  </div>
  <div class="abs newsletter">
    <div class="email">Email..</div>
    <div class="subscribe">Subscribe</div>
  </div>
  <div class="abs follow">Follow Us On :</div>
  <div class="abs socials">
    <span class="social-icon" aria-label="Share">
      <svg width="11" height="11" viewBox="0 0 11 11"><circle cx="8.5" cy="2.2" r="1.6" fill="var(--icon-line)"/><circle cx="2.5" cy="5.5" r="1.6" fill="var(--icon-line)"/><circle cx="8.5" cy="8.8" r="1.6" fill="var(--icon-line)"/><path d="M8.5 2.2L2.5 5.5L8.5 8.8" stroke="var(--icon-line)" stroke-width="1" fill="none"/></svg>
    </span>
    <span class="social-icon" aria-label="Chat">
      <svg width="11" height="11" viewBox="0 0 11 11"><path d="M1 2h9v5.5H5L2.5 9.5V7.5H1z" fill="var(--icon-line)"/></svg>
    </span>
    <span class="social-icon" aria-label="Email">
      <svg width="11" height="11" viewBox="0 0 11 11"><rect x="1" y="2.5" width="9" height="6" fill="var(--icon-line)"/><path d="M1 2.5l4.5 3.5 4.5-3.5" stroke="var(--icon-bg)" stroke-width="1" fill="none"/></svg>
    </span>
    <span class="social-icon" aria-label="Website">
      <svg width="11" height="11" viewBox="0 0 11 11"><circle cx="5.5" cy="5.5" r="4.2" stroke="var(--icon-line)" stroke-width="1.1" fill="none"/><ellipse cx="5.5" cy="5.5" rx="1.8" ry="4.2" stroke="var(--icon-line)" stroke-width="0.9" fill="none"/><line x1="1.3" y1="5.5" x2="9.7" y2="5.5" stroke="var(--icon-line)" stroke-width="0.9"/></svg>
    </span>
  </div>
  <div class="abs foot-rule"></div>
  <div class="abs copyright">Copyrights 2014 PalTote Case - All Rights Reserved</div>
</footer>

</body>
</html>
```